Business card design for Automotive workshop

We need a business card for a new automotive repair and tyre shop called Keelstone Prime Automotive located in New Zealand. We are a clean, modern and fresh workshop and company.

Front needs to feature logo,
my name:
Marlo Fenwicke (director)

Address:
48 Tarn Lane
Harrowby 3621

Phone: 07 594 2713
Mobile: 027 451 9362
Email: office@keelstoneautomotive.example.nz
Website: keelstoneautomotive.example.nz

Back needs to feature an area to write down appointment details, date and time.

Also feature a list of jobs and work we do such as,
Vehicle Servicing
All Mechanical Repairs
Warrant of Fitness
Tyres & Wheel Alignments
Automotive Diagnostics
Automotive Parts & Supplies

```html
<!DOCTYPE html>
<html lang="en">
<head>
<meta charset="utf-8">
<title>Keelstone Prime Automotive – Business Card</title>
<link rel="stylesheet" href="https://fonts.googleapis.com/css2?family=Lato:wght@400;700;900&family=Oswald:wght@600&display=swap">
<style>
  :root {
    --red: #e31e24;
    --ink: #2b2b2b;
    --black: #111111;
    --paper: #ffffff;
    --grey: #5a5a5a;
    --stage: #1f1f1f;
    --rule: #9a9a9a;
  }
  * { box-sizing: border-box; margin: 0; padding: 0; }
  html, body { width: 1200px; height: 878px; overflow: hidden; }
  body {
    background: var(--stage);
    font-family: "Lato", sans-serif;
    position: relative;
  }
  .card {
    position: absolute;
    width: 720px;
    height: 411px;
    background: var(--paper);
    overflow: hidden;
  }
  /* ---------- back ---------- */
  .card-back { left: 130px; top: 18px; }
  .back-top {
    position: absolute; inset: 0 0 auto 0; height: 232px;
    background: var(--ink);
    border-bottom: 5px solid var(--red);
    text-align: center;
    padding-top: 46px;
  }
  .brand-name {
    font-family: "Lato", sans-serif;
    font-weight: 900;
    color: var(--red);
    text-transform: uppercase;
    letter-spacing: 1px;
    white-space: nowrap;
  }
  .card-back .brand-name { font-size: 26px; margin-bottom: 26px; }
  .services { color: #f2f2f2; font-size: 16px; line-height: 1.55; letter-spacing: .2px; }
  .services .sep { color: var(--red); padding: 0 4px; }
  .appointment {
    position: absolute; top: 262px; left: 0; right: 0;
    text-align: center; color: var(--red); font-size: 17px;
  }
  .fill-row {
    position: absolute; left: 58px; right: 58px; top: 318px;
    display: flex; gap: 28px; color: var(--grey); font-size: 17px;
  }
  .fill-field { flex: 1; display: flex; align-items: flex-end; gap: 6px; }
  .fill-field .line { flex: 1; border-bottom: 1px solid var(--rule); height: 18px; }

  /* ---------- front ---------- */
  .card-front { left: 350px; top: 444px; }
  .card-front .brand-name {
    position: absolute; top: 52px; left: 0; right: 0;
    text-align: center; font-size: 36px;
  }
  .person { position: absolute; left: 40px; top: 196px; width: 300px; text-align: right; }
  .person-name {
    font-family: "Oswald", sans-serif; font-weight: 600;
    color: var(--red); font-size: 38px; letter-spacing: .5px; line-height: 1;
    text-transform: uppercase; text-align: left; white-space: nowrap;
  }
  .person-role {
    display: inline-block; color: var(--grey); font-size: 18px;
    margin-top: 6px; padding-bottom: 4px; border-bottom: 1px solid var(--red);
    min-width: 80px;
  }
  .address {
    position: absolute; left: 40px; top: 276px; width: 300px;
    color: var(--grey); font-size: 15px; line-height: 1.4;
    display: flex; justify-content: flex-end; gap: 8px; text-align: right;
    white-space: nowrap;
  }
  .divider {
    position: absolute; left: 362px; top: 196px; width: 1px; height: 116px;
    background: var(--red);
  }
  .contacts { position: absolute; left: 384px; top: 200px; list-style: none; }
  .contacts li {
    display: flex; align-items: center; gap: 10px;
    color: var(--grey); font-size: 16px; line-height: 27px; white-space: nowrap;
  }
  .contacts svg, .address svg { flex: none; }
  .bands { position: absolute; left: 0; bottom: 0; }
</style>
</head>
<body>

<section class="card card-back" aria-label="Card back">
  <div class="back-top">
    <div class="brand-name">Keelstone Prime Automotive</div>
    <p class="services">
      Vehicle Servicing<span class="sep">|</span>All Mechanical Repairs<br>
      Warrant of Fitness<span class="sep">|</span>Tyres &amp; Wheel Alignments<br>
      Automotive Diagnostics<span class="sep">|</span>Automotive Parts &amp; Supplies
    </p>
  </div>
  <div class="appointment">Appointment</div>
  <div class="fill-row">
    <div class="fill-field"><span>Date</span><span class="line"></span></div>
    <div class="fill-field"><span>Time</span><span class="line"></span></div>
  </div>
</section>

<section class="card card-front" aria-label="Card front">
  <div class="brand-name">Keelstone Prime Automotive</div>

  <div class="person">
    <div class="person-name">Marlo Fenwicke</div>
    <div class="person-role">Director</div>
  </div>
  <div class="address">
    <span>48 Tarn Lane Harrowby 3621</span>
    <svg width="12" height="16" viewBox="0 0 12 16" aria-hidden="true"><path d="M6 0C2.7 0 0 2.6 0 5.9 0 10.3 6 16 6 16s6-5.7 6-10.1C12 2.6 9.3 0 6 0zm0 8.2A2.3 2.3 0 1 1 6 3.6a2.3 2.3 0 0 1 0 4.6z" fill="var(--red)"/></svg>
  </div>

  <div class="divider"></div>

  <ul class="contacts">
    <li><svg width="13" height="13" viewBox="0 0 24 24" aria-hidden="true"><path d="M6.6 10.8a15.1 15.1 0 0 0 6.6 6.6l2.2-2.2c.3-.3.7-.4 1-.2 1.1.4 2.3.6 3.6.6.6 0 1 .4 1 1V20c0 .6-.4 1-1 1A17 17 0 0 1 3 4c0-.6.4-1 1-1h3.5c.6 0 1 .4 1 1 0 1.3.2 2.5.6 3.6.1.3 0 .7-.2 1z" fill="var(--red)"/></svg>07 594 2713</li>
    <li><svg width="13" height="13" viewBox="0 0 24 24" aria-hidden="true"><rect x="6" y="1.5" width="12" height="21" rx="2" fill="none" stroke="var(--red)" stroke-width="2.4"/><circle cx="12" cy="18.5" r="1.4" fill="var(--red)"/></svg>027 451 9362</li>
    <li><svg width="13" height="13" viewBox="0 0 24 24" aria-hidden="true"><rect x="2" y="5" width="20" height="14" rx="1.5" fill="none" stroke="var(--red)" stroke-width="2.2"/><path d="M2.5 6l9.5 7 9.5-7" fill="none" stroke="var(--red)" stroke-width="2.2"/></svg>office@keelstoneautomotive.example.nz</li>
    <li><svg width="13" height="13" viewBox="0 0 24 24" aria-hidden="true"><g fill="none" stroke="var(--red)" stroke-width="2"><circle cx="12" cy="12" r="10"/><ellipse cx="12" cy="12" rx="4.5" ry="10"/><path d="M2 12h20M4 6.5h16M4 17.5h16"/></g></svg>keelstoneautomotive.example.nz</li>
  </ul>

  <svg class="bands" width="720" height="411" viewBox="0 0 720 411" aria-hidden="true">
    <polygon points="0,350 472,350 452,370 0,370" fill="var(--black)"/>
    <polygon points="492,372 720,372 720,396 468,396" fill="var(--red)"/>
  </svg>
</section>

</body>
</html>
```